Business Card Design for a new Senior Concierge Business 1.3.24

I need a professional business card to handout at networking events for my senior helper business. I would like to use the logo I have uploaded. The design should be clear and easy to read and should list the following information...
Delia Parkhurst
Owner
www.HarborlightElderAides.com
Willowbend, Texas
936.482.5079
Delia@harborlightelderaides.com

Target Market(s)

Senior Citizens

Industry/Entity Type

Personal Helper/ Assisstant

Contact Information for Business Card

I have included the details in the project description box.

Font styles to use
Serif

Colors
0054AA
0677BA
7BADD7
CADEEF
E8F1F8
59FF00
82FF00
B8FF75
E3FFCB
F4FFEA
E54698
E96AAD
F1A4CE
F9D9EA
FCEFF6
6B429C
8869AF
B7A5CE
E3DAEB
F3F0F8

Requirements
Must have
• Include uploaded logo
Nice to have
• The log that has been uploaded
Should not have
• No crazy fonts

```html
<!DOCTYPE html>
<html lang="en">
<head>
<meta charset="utf-8">
<title>Harborlight Elder Aides – Business Card</title>
<link rel="stylesheet" href="https://fonts.googleapis.com/css2?family=Lato:wght@400;900&display=swap">
<style>
  :root {
    --stage: #2a2a2a;
    --paper: #ffffff;
    --violet: #632ce8;
    --rose: #d6195b;
    --teal: #108a8f;
    --ink: #1a1a1a;
    --white: #ffffff;
  }
  * { margin: 0; padding: 0; box-sizing: border-box; }
  html, body {
    width: 1047px; height: 1200px; overflow: hidden;
    background: var(--stage);
    font-family: "Lato", Arial, sans-serif;
  }
  .card {
    position: absolute; left: 156px; width: 743px; height: 425px;
    border-radius: 22px; overflow: hidden;
  }
  .card-front { top: 120px; background: var(--paper); }
  .card-back { top: 634px; background: var(--violet); }

  .brand { position: absolute; left: 33px; top: 28px; color: var(--violet); font-weight: 400; line-height: 1; }
  .brand-name { font-size: 44px; display: block; }
  .brand-tag { font-size: 24px; display: block; margin-top: 4px; padding-left: 2px; }

  .holder { position: absolute; right: 29px; top: 230px; text-align: right; }
  .holder-name { font-size: 35px; font-weight: 900; color: var(--rose); line-height: 1; letter-spacing: 0.2px; }
  .holder-role { font-size: 20px; font-weight: 400; color: var(--teal); margin-top: 6px; line-height: 1; }

  .divider { position: absolute; top: 301px; height: 3px; width: 222px; }
  .divider-teal { left: 33px; background: var(--teal); }
  .divider-rose { left: 262px; background: var(--rose); }
  .divider-violet { left: 490px; background: var(--violet); }

  .location { position: absolute; left: 33px; top: 373px; font-size: 18px; color: var(--ink); }

  .contacts { position: absolute; right: 29px; top: 318px; list-style: none; }
  .contact { display: flex; justify-content: flex-end; align-items: center; gap: 8px; height: 26px; font-size: 18px; color: var(--ink); }
  .contact-phone { font-size: 20px; }
  .contact svg { width: 18px; height: 18px; flex: none; }

  .back-brand {
    position: absolute; left: 0; right: 0; top: 150px; text-align: center;
    color: var(--white); font-weight: 400; line-height: 1;
  }
  .back-brand .brand-name { font-size: 74px; }
  .back-brand .brand-tag { font-size: 42px; margin-top: 10px; }
</style>
</head>
<body>
  <section class="card card-front" aria-label="Business card front">
    <div class="brand">
      <span class="brand-name">Harborlight</span>
      <span class="brand-tag">Elder Aides</span>
    </div>

    <div class="holder">
      <p class="holder-name">DELIA PARKHURST</p>
      <p class="holder-role">Owner</p>
    </div>

    <span class="divider divider-teal"></span>
    <span class="divider divider-rose"></span>
    <span class="divider divider-violet"></span>

    <p class="location">Willowbend, Texas</p>

    <ul class="contacts">
      <li class="contact contact-phone">936.482.5079
        <svg viewBox="0 0 24 24" aria-hidden="true"><path fill="#108a8f" d="M6.6 10.8a15.1 15.1 0 0 0 6.6 6.6l2.2-2.2a1 1 0 0 1 1-.25 11.4 11.4 0 0 0 3.6.57 1 1 0 0 1 1 1V20a1 1 0 0 1-1 1A17 17 0 0 1 3 4a1 1 0 0 1 1-1h3.5a1 1 0 0 1 1 1c0 1.25.2 2.45.57 3.570a1 1 0 0 1-.25 1z"/></svg>
      </li>
      <li class="contact">Delia@harborlightelderaides.com
        <svg viewBox="0 0 24 24" aria-hidden="true"><rect x="2" y="5" width="20" height="14" fill="#108a8f"/><path d="M2 5l10 8 10-8" fill="none" stroke="#fff" stroke-width="1.6"/></svg>
      </li>
      <li class="contact">HarborlightElderAides.com
        <svg viewBox="0 0 24 24" aria-hidden="true"><circle cx="12" cy="12" r="10" fill="#108a8f"/><path d="M2 12h20M12 2c3 3 3 17 0 20M12 2c-3 3-3 17 0 20" fill="none" stroke="#fff" stroke-width="1.4"/></svg>
      </li>
    </ul>
  </section>

  <section class="card card-back" aria-label="Business card back">
    <div class="back-brand">
      <span class="brand-name">Harborlight</span>
      <span class="brand-tag">Elder Aides</span>
    </div>
  </section>
</body>
</html>
```